Private Investment Firm Needs PowerPoint Presentation Template

Design PowerPoint template, take Pinebrook-submitted rough presentation draft, and drop it into new template. See attached Project Brief file for more detail.
Updates

Some decent designs have been submitted but they seem to lack the understanding of our target markets. I am hopeful that more time and feedback will result in better results.

Target Market(s)

Private company owners and intermediaries.

Font styles to use
Serif

Colors
3176b5

Requirements
Must have
• See attached Project Brief.
Nice to have
Should not have
• No B2C fluff--this is a B2B project.

```html
<!DOCTYPE html>
<html lang="en">
<head>
<meta charset="utf-8">
<title>Pinebrook Capital – Presentation Template</title>
<link href="https://fonts.googleapis.com/css2?family=Raleway:wght@400;500;600;700&display=swap" rel="stylesheet">
<style>
:root{
  --board:#a0a0a0;
  --brand:#3176b5;
  --brand-deep:#2a6cae;
  --ink:#2b2b2b;
  --muted:#4a4a4a;
  --bar:#3d3d40;
  --band:#48484b;
  --paper:#ffffff;
}
*{margin:0;padding:0;box-sizing:border-box}
html,body{width:1049px;height:1200px;overflow:hidden;background:var(--board);font-family:"Raleway",sans-serif;color:var(--ink)}
.board{position:relative;width:1049px;height:1200px}
.slide{position:absolute;width:435px;height:306px;background:var(--paper);overflow:hidden;box-shadow:0 1px 3px rgba(0,0,0,.25)}
.label{position:absolute;width:435px;text-align:center;color:#fff;font-size:20px;font-weight:400;letter-spacing:.3px}
.abs{position:absolute}
.blue-fill{background:var(--brand)}
.brand-box{position:absolute;background:#fff;border:2px solid var(--brand-deep);display:flex;align-items:center;justify-content:center;gap:10px}
.brand-box .mark{width:26px;height:26px;border-radius:50%;background:var(--brand-deep)}
.brand-name{font-family:"Raleway",sans-serif;font-weight:600;color:var(--brand-deep);font-size:19px;letter-spacing:2px}
.footer-bar{position:absolute;left:0;bottom:0;width:100%;height:27px;background:var(--bar)}
.footer-bar .foot-brand{position:absolute;left:26px;top:8px;display:flex;align-items:center;gap:4px;color:#e8e8e8;font-size:7px;font-weight:600;letter-spacing:1px}
.footer-bar .foot-brand i{display:block;width:10px;height:10px;border-radius:50%;background:#e8e8e8}
.footer-bar .foot-url{position:absolute;right:0;top:0;height:27px;width:136px;background:var(--brand);color:#fff;font-size:6px;display:flex;align-items:center;justify-content:center}
.kicker{font-size:5.5px;color:var(--muted);letter-spacing:.3px;border-bottom:.5px solid #8aa9cc;display:inline-block;padding-right:40px}
.title{font-size:12px;font-weight:500;color:#222;line-height:1.05}
.body-sm{font-size:5.5px;line-height:1.45;color:#444}
.photo{position:absolute}
ul.plain{list-style:none}
.chev{color:var(--brand);font-weight:700;margin-right:5px}
.tick{display:inline-block;width:6px;height:6px;border:.8px solid var(--brand);margin-right:4px;vertical-align:middle}
.icon{position:absolute;width:20px;height:20px;border-radius:50%;background:var(--brand);border:1.5px solid #6fa3d6}
.icon-cap{position:absolute;width:80px;text-align:center;font-size:4.6px;color:#d8d8d8;line-height:1.35}
</style>
</head>
<body>
<div class="board">

  <!-- Cover -->
  <section class="slide" style="left:71px;top:65px">
    <div class="abs blue-fill" style="left:212px;top:0;width:223px;height:306px"></div>
    <div class="brand-box" style="left:22px;top:111px;width:250px;height:83px">
      <span class="mark"></span><span class="brand-name">PINEBROOK CAPITAL</span>
    </div>
    <div class="abs" style="left:24px;top:205px;width:186px;text-align:center">
      <div style="font-size:7.4px;font-weight:700;color:var(--brand)">INTRODUCTION TO NON-CONTROL CAPITAL</div>
      <div style="font-size:5.6px;color:#555;line-height:1.45;margin-top:4px">The Lower Middle Market Private Company Strategy for<br>Raising Capital While Maintaining Business Control.</div>
      <div style="font-size:4.8px;font-weight:700;color:#333;margin-top:4px">www.pinebrookcapital.com</div>
    </div>
  </section>
  <div class="label" style="left:71px;top:383px">COVER</div>

  <!-- Inner page 1 -->
  <section class="slide" style="left:548px;top:65px">
    <div class="photo" role="img" aria-label="Black and white photo of a businessman's hand extended for a handshake" style="left:0;top:0;width:226px;height:279px;background:radial-gradient(ellipse at 55% 45%,#6a6a6a 0%,#2e2e2e 45%,#111 100%)"></div>
    <div class="abs" style="left:246px;top:36px;width:178px">
      <div class="kicker">INTRODUCTION TO</div>
      <div class="title" style="margin-top:2px">OUR COMPANY</div>
      <p class="body-sm" style="margin-top:12px">Private company owners have traditionally considered two capital raising options:</p>
      <ul class="plain body-sm" style="margin-top:8px">
        <li style="margin-bottom:6px"><span class="chev">›</span>Borrow from a local bank, or</li>
        <li style="margin-bottom:12px;padding-left:10px;text-indent:-10px"><span class="chev">›</span>Sell most or all of the company to a change-of-control investor (aka Buyout firm)</li>
        <li style="margin-bottom:10px;padding-left:10px;text-indent:-10px"><span class="tick"></span>An alternative most have not considered is the raising of Non-Control Capital, or capital that is invested into the business yet allows those same owners to retain controlling interest in their company</li>
        <li style="margin-bottom:10px;padding-left:10px;text-indent:-10px"><span class="tick"></span>Non-Control Capital is not appropriate for every private company owner but neither is a Change-of-Control sale</li>
        <li style="padding-left:10px;text-indent:-10px"><span class="tick"></span>The key is to determine what the business and owners require, and then partner with an investor best aligned with those needs so that long-term company growth, and personal goals, can both be achieved</li>
      </ul>
    </div>
    <div class="footer-bar"><div class="foot-brand"><i></i>PINEBROOK</div><div class="foot-url" style="width:136px">www.pinebrookcapital.com</div></div>
  </section>
  <div class="label" style="left:548px;top:383px">INNERPAGE-1</div>

  <!-- Inner page 2 -->
  <section class="slide" style="left:71px;top:432px">
    <div class="abs" style="left:22px;top:24px;width:190px">
      <div class="kicker">WHAT IS</div>
      <div class="title" style="margin-top:2px">NON-CONTROL CAPITAL?</div>
      <p class="body-sm" style="margin-top:5px">Non-Control Capital is an investment which is primarily used for the ongoing operation and/or growth of a business but also allows the current owners to retain:</p>
    </div>
    <div class="abs" style="left:0;top:88px;width:435px;height:106px;background:var(--band)"></div>
    <div class="icon" style="left:52px;top:97px"></div>
    <div class="icon-cap" style="left:22px;top:121px">Control of the business economics</div>
    <div class="icon" style="left:128px;top:97px"></div>
    <div class="icon-cap" style="left:98px;top:121px">Control of the business operations</div>
    <div class="icon" style="left:52px;top:149px"></div>
    <div class="icon-cap" style="left:22px;top:173px">Control of strategy and key decision making</div>
    <div class="icon" style="left:128px;top:149px"></div>
    <div class="icon-cap" style="left:98px;top:173px">Control of the Board of Directors</div>
    <div class="photo" role="img" aria-label="Laptop showing a financial chart with a rising arrow" style="left:228px;top:92px;width:184px;height:124px;border-radius:6px;background:linear-gradient(135deg,#9fb8c4,#3e5c6a 60%,#1c2a31)"></div>
    <ul class="plain abs" style="left:22px;top:208px;width:190px;font-size:5.6px;font-weight:600;color:#333;line-height:1.45">
      <li style="padding-left:10px;text-indent:-10px;margin-bottom:12px"><span class="tick"></span>Requires the alignment of management incentives with ownership</li>
      <li style="padding-left:10px;text-indent:-10px"><span class="tick"></span>In essence, a company receives the capital it needs to implement its business plans but owners continue to retain ultimate control</li>
    </ul>
    <div class="footer-bar"><div class="foot-brand"><i></i>PINEBROOK</div><div class="foot-url">www.pinebrookcapital.com</div></div>
  </section>
  <div class="label" style="left:71px;top:757px">INNERPAGE-2</div>

  <!-- Inner page 3 -->
  <section class="slide" style="left:548px;top:432px">
    <div class="abs" style="left:22px;top:23px;width:230px">
      <div class="kicker">WHEN IS</div>
      <div class="title" style="margin-top:3px">A NON-CONTROL TRANSACTION<br>APPROPRIATE?</div>
    </div>
    <ul class="plain abs body-sm" style="left:24px;top:74px;width:220px;line-height:1">
      <li style="margin-bottom:9px">The company has opportunities to expand but requires capital to do so</li>
      <li style="margin-bottom:8px">At least one active owner is not close to retirement</li>
      <li style="margin-bottom:9px">The company is not in a turnaround situation</li>
      <li style="margin-bottom:11px">Family members may work in the business and want to continue</li>
      <li style="margin-bottom:13px">Owners care about keeping the business in their family name (legacy)</li>
      <li style="margin-bottom:11px">Liquidity (dividend) is not the major use of the invested capital</li>
      <li>Owners are sensitive to utilizing too much debt</li>
    </ul>
    <div class="abs" style="left:242px;top:72px;width:.5px;height:106px;background:#ccc"></div>
    <div class="abs" style="left:251px;top:74px;width:170px;font-size:7px;color:#333">
      <div style="font-weight:600">Companies require more than just capital:</div>
      <div style="margin-top:6px">They may also need :</div>
      <ul class="plain" style="margin-top:7px;line-height:1.65">
        <li><span class="chev">›</span>operational</li>
        <li><span class="chev">›</span>marketing</li>
        <li><span class="chev">›</span>financial</li>
        <li><span class="chev">›</span>and/or technology counsel</li>
      </ul>
    </div>
    <div class="photo" role="img" aria-label="Dark blue photo of a handshake overlaid with circuit lines" style="left:0;top:195px;width:435px;height:82px;background:linear-gradient(90deg,#1d3550,#3e5d79 45%,#27445f 70%,#142a40)"></div>
    <div class="footer-bar"><div class="foot-brand"><i></i>PINEBROOK</div><div class="foot-url">www.pinebrookcapital.com</div></div>
  </section>
  <div class="label" style="left:548px;top:757px">INNERPAGE-3</div>

  <!-- Inner page 4 -->
  <section class="slide" style="left:71px;top:806px">
    <div class="photo" role="img" aria-label="Darkened photo of a team meeting around a table" style="left:0;top:0;width:435px;height:306px;background:radial-gradient(ellipse at 50% 40%,#4d4d4d,#2f2f2f 70%,#262626)"></div>
    <svg class="abs" style="left:195px;top:97px" width="36" height="36" viewBox="0 0 36 36" aria-hidden="true">
      <circle cx="18" cy="18" r="16.5" fill="#fff"/>
      <circle cx="18" cy="18" r="14" fill="var(--brand)"/>
      <path d="M11 13.5a3 3 0 1 1 3 3c0 3-1.5 5-4 6M19.5 13.5a3 3 0 1 1 3 3c0 3-1.5 5-4 6" fill="none" stroke="#fff" stroke-width="2.2" stroke-linecap="round"/>
    </svg>
    <p class="abs" style="left:88px;top:160px;width:260px;text-align:justify;font-size:6.2px;line-height:1.35;color:#eee">Our company had several business opportunities but I needed outside capital to take advantage of them. Why would I cede control of my business when we were at the exact point when raising outside capital would allow me to accelerate growth and achieve my life-long business and personal goals?!</p>
    <p class="abs" style="left:88px;top:193px;width:260px;text-align:center;font-size:5px;color:#6da3dc">--Mark Ellison, CEO, The Norfield Group</p>
  </section>
  <div class="label" style="left:71px;top:1127px">INNERPAGE-4</div>

  <!-- Back -->
  <section class="slide" style="left:548px;top:803px">
    <div class="abs blue-fill" style="left:0;top:0;width:227px;height:306px"></div>
    <div class="brand-box" style="left:163px;top:111px;width:250px;height:84px">
      <span class="mark"></span><span class="brand-name">PINEBROOK CAPITAL</span>
    </div>
    <div class="abs" style="left:227px;top:274px;width:208px;text-align:center;font-size:7px;font-weight:700;color:#222">www.pinebrookcapital.com</div>
  </section>
  <div class="label" style="left:548px;top:1127px">BACK</div>

</div>
</body>
</html>
```